Meridale Nutrition needs Stationary and a business card

We would like to use our current logo. The text can be moved around as needed. The stationary needs to be a 'first page' where the logo is more prominent to be impressive on higher quality paper and a second page where the logo is more subtle where there will be much more information on the page. There are 2 clinic locations which will need include name, address, phone number, fax number, web address. The business card should be single sided and contain this information also.
The design must be contemporary and sophisticated as this is a science based diet run out of a medical clinic.

Target Market(s)

People wanting to lose weight, athletes looking to optimise performance, people with arthritis or fighting cancer

Industry/Entity Type

Business

Contact Information for Business Card

must use the logo. I have attached an example card with the practice details on it. there must be space for the doctors name. Also the website www.meridalenutrition.com.au

Requirements
Must have
• the logo, the business adresses and phone numbers, the website, the doctors name and qualifications
Nice to have
• some creativity
Should not have
• Do not simply reproduce the existing card please

```html
<!DOCTYPE html>
<html lang="en">
<head>
<meta charset="utf-8">
<title>Meridale Nutrition – Business Card</title>
<link rel="stylesheet" href="https://fonts.googleapis.com/css2?family=Open+Sans:wght@400;600;700&display=swap">
<style>
  :root {
    --page-bg: #e9ebee;
    --card-white: #ffffff;
    --brand-blue: #2c5f95;
    --brand-blue-dark: #244f7e;
    --accent-cyan: #2fb7e6;
    --logo-sky: #4cc3ee;
    --text-grey: #4a4a4a;
    --divider: #d9dde2;
  }
  * { box-sizing: border-box; margin: 0; padding: 0; }
  html, body {
    width: 1200px; height: 950px; overflow: hidden;
    background: var(--page-bg);
    font-family: "Open Sans", Arial, sans-serif;
  }
  .stage {
    width: 1200px; height: 950px;
    display: flex; align-items: center; justify-content: center;
  }
  .business-card {
    position: relative;
    width: 1000px; height: 611px;
    background: var(--card-white);
    box-shadow: 0 10px 30px rgba(0,0,0,0.18);
    overflow: hidden;
  }
  .logo-block {
    position: absolute; left: 70px; top: 70px; width: 300px;
    display: flex; flex-direction: column; align-items: center;
  }
  .logo-mark {
    width: 170px; height: 170px; border-radius: 50%;
    background: radial-gradient(circle at 40% 35%, var(--logo-sky), var(--brand-blue) 85%);
  }
  .logo-name {
    margin-top: 26px;
    font-weight: 700; font-size: 30px; line-height: 1.15;
    color: var(--brand-blue); text-align: center;
  }
  .column-divider {
    position: absolute; left: 420px; top: 40px;
    width: 1px; height: 370px; background: var(--divider);
  }
  .practitioner {
    position: absolute; left: 460px; top: 38px; right: 40px;
    color: var(--text-grey);
  }
  .doctor-name {
    font-size: 34px; font-weight: 700; color: var(--brand-blue); line-height: 1.2;
  }
  .qualifications {
    margin-top: 6px; font-size: 17px; font-weight: 600;
    color: var(--accent-cyan); line-height: 1.35;
  }
  .clinic { margin-top: 20px; font-size: 19px; line-height: 1.35; }
  .clinic-name { font-weight: 700; color: var(--brand-blue); }
  .tel-label { font-weight: 700; color: var(--brand-blue); }
  .accent-stripe {
    position: absolute; left: 0; right: 0; top: 452px;
    height: 5px; background: var(--accent-cyan);
  }
  .footer-band {
    position: absolute; left: 0; right: 0; top: 461px; bottom: 0;
    background: linear-gradient(180deg, var(--brand-blue), var(--brand-blue-dark));
    display: flex; justify-content: space-between; align-items: center;
    padding: 0 44px;
  }
  .speciality { font-size: 22px; font-weight: 600; color: var(--accent-cyan); line-height: 1.3; }
  .web { font-size: 21px; color: #ffffff; line-height: 1.3; }
  .footer-right { text-align: right; }
</style>
</head>
<body>
<main class="stage">
  <article class="business-card">
    <div class="logo-block">
      <div class="logo-mark"></div>
      <div class="logo-name">Meridale<br>Nutrition</div>
    </div>

    <div class="column-divider"></div>

    <section class="practitioner">
      <h1 class="doctor-name">Dr Elias Marren</h1>
      <p class="qualifications">MBBS (NSW) MBiomedE FRACS (Ortho)<br>FAOrthA Orthopaedic Surgeon</p>
      <div class="clinic">
        <div class="clinic-name">Ashcombe</div>
        <div>12-14 Harlow Street</div>
        <div>Ashcombe NSW 2140</div>
        <div><span class="tel-label">Tel:</span> 02 9555 0142</div>
      </div>
      <div class="clinic">
        <div class="clinic-name">Westbury</div>
        <div>88 Linden Avenue</div>
        <div>Westbury NSW 2035</div>
        <div><span class="tel-label">Tel:</span> 02 9555 0187</div>
      </div>
    </section>

    <div class="accent-stripe"></div>

    <footer class="footer-band">
      <div class="footer-left">
        <div class="speciality">Shoulder and Elbow</div>
        <div class="web">www.meridalenutrition.com.au</div>
      </div>
      <div class="footer-right">
        <div class="speciality">Knee surgery</div>
        <div class="web">www.marrenknee.com.au</div>
      </div>
    </footer>
  </article>
</main>
</body>
</html>
```